Veldmark Supplies Business Card

Professional business card that stand out to our potential customers. Front and back with clean modern design

Industry/Entity Type

Oil and gas

Contact Information for Business Card

Name, address, website , office phone and cell number

Requirements
Must have
• Editable files for each employee

```html
<!DOCTYPE html>
<html lang="en">
<head>
<meta charset="utf-8">
<title>Veldmark Supplies Business Card</title>
<link rel="stylesheet" href="https://fonts.googleapis.com/css2?family=Roboto:wght@400;500;700;900&display=swap">
<style>
  :root {
    --backdrop: #2b2b2b;
    --card-black: #1c1c1e;
    --card-back: #1f1f21;
    --emboss: #4a4a4d;
    --brand-red: #e01b22;
    --brand-blue: #28b4d8;
    --ink-dark: #1c1c1e;
    --ink-white: #ffffff;
    --ink-soft: #e6e6e6;
  }
  * { margin: 0; padding: 0; box-sizing: border-box; }
  html, body { width: 1200px; height: 852px; overflow: hidden; }
  body {
    background: var(--backdrop);
    font-family: "Roboto", Arial, sans-serif;
    position: relative;
  }
  .card {
    position: absolute;
    width: 480px;
    height: 274px;
    border-radius: 18px;
    overflow: hidden;
    top: 289px;
  }
  .card--back { left: 90px; background: var(--card-back); }
  .card--front { left: 630px; background: var(--card-black); }

  .back-mark {
    position: absolute;
    inset: 0;
    display: flex;
    align-items: center;
    justify-content: center;
    gap: 12px;
  }
  .back-mark__square { width: 22px; height: 22px; background: var(--emboss); }
  .back-mark__name {
    color: var(--emboss);
    font-weight: 900;
    font-size: 26px;
    letter-spacing: 1px;
    text-transform: uppercase;
  }

  .front-wave { position: absolute; inset: 0; }

  .front-square {
    position: absolute;
    left: 26px;
    top: 20px;
    width: 40px;
    height: 40px;
    background: var(--brand-red);
  }
  .banner {
    position: absolute;
    left: 78px;
    top: 22px;
    width: 376px;
    height: 32px;
    display: flex;
    color: var(--ink-dark);
    font-weight: 900;
    font-size: 21px;
    letter-spacing: 1.5px;
    text-transform: uppercase;
  }
  .banner__part {
    flex: 1;
    display: flex;
    align-items: center;
    justify-content: center;
  }
  .banner__part--red { background: var(--brand-red); }
  .banner__part--blue { background: var(--brand-blue); }

  .holder { position: absolute; left: 30px; top: 118px; }
  .holder__name { color: var(--brand-blue); font-weight: 700; font-size: 17px; }
  .holder__role { color: var(--ink-white); font-size: 11px; margin-top: 2px; }

  .contact {
    position: absolute;
    right: 22px;
    top: 100px;
    list-style: none;
    text-align: right;
    color: var(--ink-white);
    font-size: 10.5px;
    line-height: 19px;
  }
  .contact li { display: flex; align-items: center; justify-content: flex-end; gap: 6px; }
  .contact svg { width: 10px; height: 10px; fill: var(--ink-soft); }
</style>
</head>
<body>
  <section class="card card--back" aria-label="Card back">
    <div class="back-mark">
      <span class="back-mark__square"></span>
      <span class="back-mark__name">Veldmark Supplies</span>
    </div>
  </section>

  <section class="card card--front" aria-label="Card front">
    <svg class="front-wave" viewBox="0 0 480 274" aria-hidden="true">
      <path d="M480,62 C420,64 380,84 330,112 C290,134 255,146 215,152 C150,162 80,228 0,236 L0,274 L480,274 Z" fill="var(--brand-red)"/>
      <path d="M480,50 C420,52 378,72 328,100 C288,122 252,134 212,140 C148,150 78,216 0,224" fill="none" stroke="var(--brand-blue)" stroke-width="6"/>
      <path d="M212,148 C148,158 80,224 20,230" fill="none" stroke="var(--brand-blue)" stroke-width="2"/>
    </svg>

    <span class="front-square"></span>
    <div class="banner">
      <span class="banner__part banner__part--red">Veldmark</span>
      <span class="banner__part banner__part--blue">Supplies</span>
    </div>

    <div class="holder">
      <p class="holder__name">John Doe Smith</p>
      <p class="holder__role">Managing Director</p>
    </div>

    <ul class="contact">
      <li>(555)201-4837
        <svg viewBox="0 0 10 10"><path d="M2 0.5 L3.8 2.5 L2.8 3.6 C3.4 5 5 6.6 6.4 7.2 L7.5 6.2 L9.5 8 L8.4 9.5 C4.5 9.3 0.7 5.5 0.5 1.6 Z"/></svg>
      </li>
      <li>www.veldmarksupplies.com
        <svg viewBox="0 0 10 10"><circle cx="5" cy="5" r="4.3" fill="none" stroke="var(--ink-soft)" stroke-width="1.2"/><path d="M0.8 5 H9.2 M5 0.8 V9.2" stroke="var(--ink-soft)" stroke-width="0.9"/></svg>
      </li>
      <li>sales@veldmarksupplies.com
        <svg viewBox="0 0 10 10"><rect x="0.5" y="2" width="9" height="6.5"/><path d="M0.5 2 L5 5.6 L9.5 2" fill="none" stroke="var(--brand-red)" stroke-width="0.9"/></svg>
      </li>
      <li>412 Harlan Ridge Suite 5 Midland, Tx 79701</li>
    </ul>
  </section>
</body>
</html>
```